Meridian Crestline Motors *

Professional business cards for our auto wholesale dealership.

Target Market(s)

New and used cars sales managers and middle class to higher end private party buyers.

Industry/Entity Type

Automotive

Contact Information for Business Card

Meridian Crestline Motors
Darnell R Okonski
Owner
(555) 304-6618
mercrestmotors@quillbox.example
Dealer Lic # 48265

Logo Text

Meridian Crestline Motors, Mer Crest Motors, MCM, etc

Font styles to use
Serif
Sans Serif

Colors

Designer to choose colors to be used in the design.

Requirements
Must have
• A professional, but not pretentious, look
Nice to have
• It might be nice to see "MCM" in a shape form i.e. circle, triangle, etc in the corner or background somehwere
Should not have
• bright "girly" colors

```html
<!DOCTYPE html>
<html lang="en">
<head>
<meta charset="utf-8">
<title>Meridian Crestline Motors – Business Cards</title>
<link href="https://fonts.googleapis.com/css2?family=Lato:wght@400;700;900&display=swap" rel="stylesheet">
<style>
  :root {
    --bg: #d6d6d6;
    --card: #ffffff;
    --brand-red: #c4161c;
    --ink: #222222;
    --muted: #555555;
    --rule: #333333;
  }
  html, body {
    margin: 0;
    padding: 0;
    width: 1200px;
    height: 800px;
    overflow: hidden;
    background: var(--bg);
    font-family: "Lato", Arial, sans-serif;
  }
  .canvas {
    width: 1200px;
    height: 800px;
    display: flex;
    align-items: center;
    justify-content: center;
    gap: 40px;
  }
  .card {
    position: relative;
    width: 540px;
    height: 309px;
    background: var(--card);
    box-shadow: 0 2px 6px rgba(0,0,0,0.12);
    box-sizing: border-box;
  }

  /* Brand lockup */
  .brand {
    display: flex;
    align-items: center;
    gap: 12px;
  }
  .brand-mark {
    width: 46px;
    height: 46px;
    background: var(--brand-red);
    flex: none;
  }
  .brand-name {
    font-weight: 900;
    color: var(--brand-red);
    text-transform: uppercase;
    line-height: 1.05;
    letter-spacing: 0.5px;
  }

  /* Front */
  .card-front {
    display: flex;
    align-items: center;
    justify-content: center;
  }
  .card-front .brand-name { font-size: 24px; }
  .card-front .brand-mark { width: 58px; height: 58px; }

  /* Back */
  .card-back { padding: 34px 30px 0 30px; }
  .contact-name {
    margin: 0;
    font-size: 22px;
    font-weight: 700;
    color: var(--brand-red);
    letter-spacing: 0.3px;
  }
  .contact-role {
    margin: 0 0 12px;
    font-size: 13px;
    color: var(--muted);
  }
  .contact-list {
    list-style: none;
    margin: 0;
    padding: 0;
    font-size: 13px;
    color: var(--ink);
  }
  .contact-list li {
    display: flex;
    align-items: center;
    gap: 8px;
    margin-bottom: 4px;
  }
  .contact-icon {
    width: 13px;
    height: 13px;
    background: var(--brand-red);
    display: inline-flex;
    align-items: center;
    justify-content: center;
    flex: none;
  }
  .card-back .brand {
    position: absolute;
    top: 96px;
    right: 30px;
    gap: 8px;
  }
  .card-back .brand-name { font-size: 15px; }
  .card-back .brand-mark { width: 36px; height: 36px; }
  .divider {
    position: absolute;
    left: 30px;
    right: 30px;
    top: 206px;
    border: 0;
    border-top: 1px solid var(--rule);
    margin: 0;
  }
  .dealer-license {
    position: absolute;
    right: 30px;
    top: 220px;
    margin: 0;
    font-size: 14px;
    color: var(--ink);
  }
</style>
</head>
<body>
<main class="canvas">

  <section class="card card-front" aria-label="Card front">
    <div class="brand">
      <span class="brand-mark"></span>
      <span class="brand-name">Meridian<br>Crestline Motors</span>
    </div>
  </section>

  <section class="card card-back" aria-label="Card back">
    <h1 class="contact-name">Darnell R Okonski</h1>
    <p class="contact-role">Owner</p>
    <ul class="contact-list">
      <li>
        <span class="contact-icon">
          <svg width="9" height="9" viewBox="0 0 24 24" aria-hidden="true"><path fill="#fff" d="M6.6 10.8a15 15 0 0 0 6.6 6.6l2.2-2.2a1 1 0 0 1 1-.25 11.4 11.4 0 0 0 3.6.57 1 1 0 0 1 1 1V20a1 1 0 0 1-1 1A17 17 0 0 1 3 4a1 1 0 0 1 1-1h3.5a1 1 0 0 1 1 1c0 1.25.2 2.45.57 3.57a1 1 0 0 1-.25 1z"/></svg>
        </span>
        (555) 304-6618
      </li>
      <li>
        <span class="contact-icon">
          <svg width="9" height="9" viewBox="0 0 24 24" aria-hidden="true"><path fill="none" stroke="#fff" stroke-width="2.5" d="M3 6h18v12H3z M3 6l9 7 9-7"/></svg>
        </span>
        mercrestmotors@quillbox.example
      </li>
    </ul>

    <div class="brand">
      <span class="brand-mark"></span>
      <span class="brand-name">Meridian<br>Crestline Motors</span>
    </div>

    <hr class="divider">
    <p class="dealer-license">Dealer Lic # 48265</p>
  </section>

</main>
</body>
</html>
```